Commercial Real Estate

We need a business card design for a new commercial real estate business that specializes in apartment building brokerage. Not individual units but the entire complex. We find and represent the owners existing buildings and well as new buyers for those buildings. The design should convey trust, integrity, knowledge and growth. It should be easily read.

Target Market(s)

40 to 65 years old

Industry/Entity Type

Real Estate

```html
<!DOCTYPE html>
<html lang="en">
<head>
<meta charset="utf-8">
<title>Quillmere Business Card</title>
<link rel="stylesheet" href="https://fonts.googleapis.com/css2?family=Lato:wght@400;700;900&display=swap">
<style>
  :root {
    --backdrop: #2a2a2a;
    --card: #ffffff;
    --card-shade: #eceeee;
    --teal: #5bbcbc;
    --slate: #3d4a4a;
    --ink: #3a3a3a;
  }
  * { margin: 0; padding: 0; box-sizing: border-box; }
  html, body {
    width: 1200px; height: 900px; overflow: hidden;
    background: var(--backdrop);
    font-family: "Lato", sans-serif;
  }
  .card {
    position: absolute; left: 100px; top: 164px;
    width: 1000px; height: 572px;
    background: linear-gradient(135deg, var(--card) 0%, var(--card) 55%, var(--card-shade) 100%);
    overflow: hidden;
    box-shadow: 0 18px 40px rgba(0,0,0,.55);
  }
  .holder { position: absolute; left: 110px; top: 130px; }
  .holder-name {
    color: var(--teal); font-weight: 900; font-size: 40px; letter-spacing: .5px; line-height: 1;
  }
  .holder-role {
    color: var(--ink); font-weight: 700; font-size: 24px; letter-spacing: .5px; margin-top: 6px;
  }
  .icon-tab {
    position: absolute; left: 0; top: 300px; width: 72px; height: 240px;
    background: var(--teal); border-radius: 0 14px 14px 0;
    display: flex; flex-direction: column; justify-content: space-around; align-items: center;
    padding: 10px 0;
  }
  .icon-tab svg { width: 34px; height: 34px; }
  .contacts {
    position: absolute; left: 110px; top: 318px; list-style: none;
  }
  .contacts li {
    color: var(--ink); font-weight: 700; font-size: 26px; height: 58px; line-height: 40px;
    white-space: nowrap;
  }
  .brand {
    position: absolute; left: 620px; top: 150px; width: 340px;
    display: flex; flex-direction: column; align-items: center; gap: 22px;
  }
  .brand-dot { width: 110px; height: 110px; border-radius: 50%; background: var(--teal); }
  .brand-name {
    color: var(--slate); font-weight: 900; font-size: 48px; letter-spacing: 2px; line-height: 1;
    white-space: nowrap;
  }
  .base-band {
    position: absolute; left: 0; bottom: 0; width: 100%; height: 16px; background: var(--teal);
  }
  .base-corner {
    position: absolute; right: 0; bottom: 0; width: 340px; height: 34px;
    background: var(--slate); border-top-left-radius: 34px;
    box-shadow: -4px -4px 0 0 var(--card);
  }
</style>
</head>
<body>
  <section class="card">
    <div class="holder">
      <p class="holder-name">YOUR NAME</p>
      <p class="holder-role">DESIGNATION</p>
    </div>

    <div class="icon-tab">
      <svg viewBox="0 0 24 24" fill="none" stroke="#fff" stroke-width="1.8" aria-label="Phone"><rect x="6" y="2" width="12" height="20" rx="2"/><line x1="10" y1="18.5" x2="14" y2="18.5"/></svg>
      <svg viewBox="0 0 24 24" fill="none" stroke="#fff" stroke-width="1.8" aria-label="Email"><rect x="2" y="5" width="20" height="14" rx="1"/><polyline points="2,5 12,13 22,5"/></svg>
      <svg viewBox="0 0 24 24" fill="none" stroke="#fff" stroke-width="1.8" aria-label="Website"><circle cx="12" cy="12" r="10"/><ellipse cx="12" cy="12" rx="4" ry="10"/><line x1="2" y1="12" x2="22" y2="12"/></svg>
      <svg viewBox="0 0 24 24" fill="#fff" aria-label="Address"><path d="M12 2a7 7 0 0 0-7 7c0 5 7 13 7 13s7-8 7-13a7 7 0 0 0-7-7zm0 9.5a2.5 2.5 0 1 1 0-5 2.5 2.5 0 0 1 0 5z"/></svg>
    </div>

    <ul class="contacts">
      <li>0400 518 276</li>
      <li>info@quillmere.example</li>
      <li>www.quillmere.example</li>
      <li>Your Complete Address Details Here</li>
    </ul>

    <div class="brand">
      <span class="brand-dot"></span>
      <span class="brand-name">QUILLMERE</span>
    </div>

    <div class="base-band"></div>
    <div class="base-corner"></div>
  </section>
</body>
</html>
```